Flyer-Design für psychologische Beratungspraxis für Mütter
Vielen herzlichen Dank! Super Kommunikation, alle Änderungswünsche wurden sofort umgesetzt, auch hin und her meinerseits war kein Problem, immer wieder. Schnelle Reaktion, tolle Ideen. Ich bin super zufrieden und würde jederzeit sehr gerne wieder mit brightfoxes zusammenarbeiten! Toller Flyer, ich liebe meinen neuen Flyer! :)
Zielgruppe
Gelassenheitswerkstatt ist eine psychologische Beratungspraxis. Ich unterstütze Mütter, Schwangere und Frauen mit Kinderwunsch bei Herausforderungen rund um Schwangerschaft, Geburt, Mutterschaft, und damit einhergehenden Problemen.
Aufgabenstellung
Text nochmal geringgradig geändert...siehe Datei anbei

```html
<!DOCTYPE html>
<html lang="de">
<head>
<meta charset="utf-8">
<title>Flyer Gelassenheitswerkstatt</title>
<link rel="stylesheet" href="https://fonts.googleapis.com/css2?family=Amatic+SC:wght@700&family=Arimo:wght@400;700&display=swap">
<style>
  :root {
    --bg: #e8e7e4;
    --paper: #fbfbfa;
    --navy: #3b3f8e;
    --navy-soft: #5a5fa6;
    --sky-top: #7f9fb7;
    --sky-mid: #a9c0d1;
    --sky-low: #c9d8e3;
    --hair: #d8a86a;
    --accent: #e2512b;
  }
  * { box-sizing: border-box; margin: 0; padding: 0; }
  html, body { width: 1200px; height: 864px; overflow: hidden; background: var(--bg); }
  body { font-family: "Arimo", Arial, sans-serif; color: var(--navy); }

  .flyer {
    position: absolute; left: 50px; top: 160px;
    width: 1100px; height: 544px;
    display: flex;
    box-shadow: 0 18px 40px rgba(0,0,0,.12);
  }
  .panel-back {
    position: relative; width: 430px; height: 100%;
    background: var(--paper);
  }
  .portrait {
    position: absolute; left: 34px; top: 34px;
    width: 190px; height: 190px; border-radius: 50%;
    background: radial-gradient(circle at 50% 40%, #e4d2bd 0%, #cdb59a 60%, #b89c80 100%);
  }
  .brand {
    position: absolute; left: 244px; top: 96px;
    display: flex; align-items: center; gap: 8px;
    font-weight: 700; font-size: 13px; color: var(--navy);
  }
  .brand-dot { width: 18px; height: 18px; border-radius: 50%; background: var(--accent); flex: none; }
  .contact { position: absolute; left: 40px; top: 276px; line-height: 1.35; }
  .contact h2 { font-size: 17px; font-weight: 700; letter-spacing: .3px; margin-bottom: 14px; }
  .contact .name { font-weight: 700; font-size: 14px; }
  .contact p { font-size: 14px; color: var(--navy-soft); }
  .contact .web { margin-top: 18px; }
  .contact .phone { margin-top: 18px; }
  .flags { position: absolute; right: 34px; bottom: 40px; display: flex; gap: 7px; }
  .flags svg { width: 26px; height: 16px; display: block; }

  .panel-image {
    position: relative; flex: 1; height: 100%;
    background:
      radial-gradient(ellipse 160px 90px at 88% 35%, rgba(255,255,255,.45), transparent 70%),
      radial-gradient(ellipse 120px 70px at 10% 55%, rgba(255,255,255,.35), transparent 70%),
      linear-gradient(180deg, var(--sky-top) 0%, var(--sky-mid) 55%, var(--sky-low) 100%);
  }
  .photo-figures {
    position: absolute; left: 330px; top: 170px; width: 260px; height: 374px;
    border-radius: 130px 130px 0 0;
    background: linear-gradient(180deg, var(--hair) 0%, #b98a58 45%, #8d857d 75%, #7d7873 100%);
    opacity: .85;
  }
  .fold { position: absolute; left: 135px; top: 0; bottom: 0; width: 1px; background: rgba(255,255,255,.35); }
  .cover { position: absolute; left: 135px; right: 0; top: 0; bottom: 0; }
  .title { position: absolute; left: 40px; top: 40px; display: flex; flex-direction: column; gap: 8px; }
  .title span {
    display: inline-block; align-self: flex-start;
    background: #fff; border-radius: 22px; padding: 2px 22px 0;
    font-family: "Amatic SC", cursive; font-size: 34px; line-height: 40px; color: var(--navy);
  }
  .title span + span { margin-left: 34px; }
  .subtitle { position: absolute; left: 84px; top: 150px; font-size: 13px; font-weight: 700; line-height: 1.35; color: var(--navy); }
  .cover-brand {
    position: absolute; right: 40px; top: 236px;
    display: flex; align-items: center; gap: 7px;
    font-weight: 700; font-size: 12px; color: rgba(255,255,255,.8);
  }
  .cover-brand .brand-dot { background: rgba(255,255,255,.8); width: 14px; height: 14px; }
</style>
</head>
<body>
<main class="flyer">
  <section class="panel-back">
    <div class="portrait" role="img" aria-label="Porträtfoto der Beraterin"></div>
    <div class="brand"><span class="brand-dot"></span>Gelassenheitswerkstatt</div>
    <div class="contact">
      <h2>KRISENBEGLEITUNG &amp; LEBENSBERATUNG</h2>
      <p class="name">Dr. Helena Marchetti</p>
      <p>Systemische Beraterin (VSBD)</p>
      <p>Heilpraktikerin für Psychotherapie</p>
      <p class="web">www.gelassenheitswerkstatt.de</p>
      <p>info@gelassenheitswerkstatt.de</p>
      <p class="phone">0152 481 27 530</p>
    </div>
    <div class="flags" aria-label="Sprachen: Deutsch, Italienisch, Englisch, Französisch">
      <svg viewBox="0 0 26 16"><rect width="26" height="5.34" fill="#222"/><rect y="5.33" width="26" height="5.34" fill="#d22"/><rect y="10.66" width="26" height="5.34" fill="#f6c500"/></svg>
      <svg viewBox="0 0 26 16"><rect width="8.7" height="16" fill="#1a9a46"/><rect x="8.66" width="8.7" height="16" fill="#fff"/><rect x="17.33" width="8.7" height="16" fill="#d22"/></svg>
      <svg viewBox="0 0 26 16"><rect width="26" height="16" fill="#233a84"/><path d="M0 0L26 16M26 0L0 16" stroke="#fff" stroke-width="3"/><path d="M0 0L26 16M26 0L0 16" stroke="#c8102e" stroke-width="1"/><path d="M13 0V16M0 8H26" stroke="#fff" stroke-width="5"/><path d="M13 0V16M0 8H26" stroke="#c8102e" stroke-width="3"/></svg>
      <svg viewBox="0 0 26 16"><rect width="8.7" height="16" fill="#233a84"/><rect x="8.66" width="8.7" height="16" fill="#fff"/><rect x="17.33" width="8.7" height="16" fill="#d22"/></svg>
    </div>
  </section>
  <section class="panel-image" role="img" aria-label="Foto: Mutter hält ihr Kind im Arm vor hellblauem Wolkenhimmel">
    <div class="photo-figures"></div>
    <div class="fold"></div>
    <div class="cover">
      <h1 class="title"><span>KRISENBEGLEITUNG</span><span>UND LEBENSBERATUNG</span></h1>
      <p class="subtitle">Psychologische Beratungspraxis für Mütter,<br>Schwangere und Frauen mit Kinderwunsch</p>
      <div class="cover-brand"><span class="brand-dot"></span>Gelassenheitswerkstatt</div>
    </div>
  </section>
</main>
</body>
</html>
```